Email Preference Page Design

We are looking for a 2 page design for our users to edit their email preferences and submit friend referrals. You can find the fuctionality, content and text here:

https://brightvanta.mailrelayhub.example/app/linkClick/7281/5fa9c1d3b07e442b/28374615/9bd4e01a7c3f2a65

* the shipping and billing address might be different so you need to show the billing if the "same as shipping" box is not checked. It can auto-hide like the page above shows if that fits your design.

* when the "unsubscribe from all email lists" box is selected, all the other checkbox options will hide as in the example page. We need you to show us what the site will look like with and without that checkbox selected.

We want to match these two pages to the general feel of these website pages:

www.brightvanta.com
and
free.brightvanta.com

The page should be very clean and tight. Project is for design only but must be able to be implemented in html showing button and checkbox states. Technically this must be two pages for our system - one for all the user info and one for individual email referrals (see example above).

Target Market(s)

video professionals

Industry/Entity Type

Shipping

Requirements
Must have
• our logo (see numerous versions attached)
well designed header
well designed sections
clean editable text
tight layout
html friendly
easy to understand
2 pages
Nice to have
• custom checkboxes and radio buttons

```html
<!DOCTYPE html>
<html lang="en">
<head>
<meta charset="utf-8">
<title>Brightvanta – Communication Preferences</title>
<link rel="stylesheet" href="https://fonts.googleapis.com/css2?family=Open+Sans:ital,wght@0,400;0,600;0,700;1,400&family=Exo+2:wght@300&display=swap">
<style>
:root{
  --navy:#26323c;
  --orange:#f68b33;
  --orange-dark:#c9702a;
  --field:#effcfd;
  --field-border:#b86a2c;
  --paper:#ebebeb;
  --ink:#2c2c2c;
  --muted:#3b3b3b;
  --white:#ffffff;
}
*{box-sizing:border-box;margin:0;padding:0}
html,body{width:1200px;height:2624px;overflow:hidden;background:var(--paper)}
body{font-family:"Open Sans",Arial,sans-serif;color:var(--ink)}
.stage{position:absolute;left:0;top:0;width:686px;height:1500px;transform:scale(1.749271);transform-origin:0 0}
.abs{position:absolute}
.top-bar{left:0;top:0;width:686px;height:30px;background:var(--navy)}
.hero{left:0;top:0;width:686px;height:713px;background:var(--orange);z-index:0}
.top-bar{z-index:1}
.brand-tab{left:165px;top:0;width:356px;height:84px;z-index:2}
.brand{left:165px;top:20px;width:356px;display:flex;justify-content:center;align-items:center;gap:8px;z-index:3}
.brand-dot{width:18px;height:18px;border-radius:50%;background:var(--orange)}
.brand-name{font-size:34px;font-weight:600;color:var(--navy);letter-spacing:-0.5px;line-height:40px}
.page-title{left:0;top:112px;width:686px;text-align:center;font-family:"Exo 2","Open Sans",sans-serif;font-weight:300;font-size:40px;color:var(--white);letter-spacing:.5px}
.required-tag{left:295px;top:168px;width:96px;height:18px;background:var(--navy);color:var(--white);font-size:10px;line-height:18px;text-align:center}
.required-rule{left:285px;top:186px;width:116px;height:1px;background:var(--navy)}
.section-head{font-size:17px;font-weight:600;color:var(--white)}
.section-rule{height:2px;background:var(--white)}
.notch{width:0;height:0;border-left:5px solid transparent;border-right:5px solid transparent;border-top:6px solid var(--white)}
.label{width:110px;text-align:right;font-size:12px;color:var(--white);line-height:30px}
.label.wide{width:100px;text-align:right}
.field{height:30px;background:var(--field);border:1px solid var(--field-border);box-shadow:inset 0 2px 3px rgba(0,0,0,.12);font-size:12px;color:#555;line-height:28px;padding-left:8px}
.field.focus{background:var(--white);border-color:#8a4d1d}
.select-arrow{right:0;top:0;width:23px;height:28px;border-left:1px solid #cfd8d9;color:#999;font-size:10px;text-align:center;line-height:28px}
.plus{font-size:12px;color:var(--white);line-height:30px}
.box{width:14px;height:14px;background:#f4f6f7;border:1px solid #9aa3a8;box-shadow:inset 0 1px 2px rgba(0,0,0,.15)}
.same-text{left:386px;top:266px;font-size:17px;line-height:20px;color:var(--white)}
.divider-mark{left:317px;top:687px;width:52px;height:52px;border-radius:50%;background:var(--orange)}
.footer{left:0;top:1447px;width:686px;height:53px;background:var(--navy)}
.subscribe{left:51px;top:783px;font-size:17px;font-weight:700;color:var(--ink)}
.subscribe-note{left:51px;top:804px;font-size:16px;font-style:italic;color:var(--muted)}
.filter-note{left:29px;top:835px;font-size:17px;font-weight:700;color:var(--orange)}
.list-head{height:54px;background:var(--navy);color:var(--white);font-size:17px;font-weight:600;line-height:17px;padding:8px 16px}
.list-notch{width:0;height:0;border-left:6px solid transparent;border-right:6px solid transparent;border-top:7px solid var(--navy)}
.opt{font-size:12.5px;color:var(--ink);line-height:16px}
.unsubscribe{left:363px;top:1195px;width:292px;height:37px;background:var(--orange);border:1px solid var(--orange-dark);color:var(--white);font-weight:700;font-size:16px;line-height:35px;padding-left:29px}
.unsubscribe .box{left:9px;top:11px;background:var(--white)}
.submit{left:29px;top:1363px;width:207px;height:46px;background:var(--orange);border:1px solid var(--orange-dark);color:var(--white);font-size:22px;font-weight:600;line-height:44px;padding-left:34px}
</style>
</head>
<body>
<div class="stage">
  <div class="abs hero"></div>
  <div class="abs top-bar"></div>
  <svg class="abs brand-tab" viewBox="0 0 356 84" aria-hidden="true">
    <path d="M0 0H356V70Q178 88 0 70Z" fill="#ffffff"/>
  </svg>
  <div class="abs brand"><span class="brand-dot"></span><span class="brand-name">brightvanta</span></div>

  <h1 class="abs page-title">Communication Preferences</h1>
  <div class="abs required-tag">Required Fields*</div>
  <div class="abs required-rule"></div>

  <!-- Contact & Billing -->
  <h2 class="abs section-head" style="left:29px;top:222px">Contact &amp; Billing</h2>
  <div class="abs section-rule" style="left:29px;top:249px;width:292px"></div>
  <div class="abs notch" style="left:38px;top:251px"></div>

  <div class="abs label" style="left:5px;top:269px">First Name*</div>
  <div class="abs field" style="left:122px;top:269px;width:198px"></div>
  <div class="abs label" style="left:5px;top:303px">Last Name*</div>
  <div class="abs field focus" style="left:122px;top:303px;width:198px"></div>
  <div class="abs label" style="left:5px;top:337px">Email*</div>
  <div class="abs field" style="left:122px;top:337px;width:198px"></div>
  <div class="abs label" style="left:5px;top:371px">Phone</div>
  <div class="abs field" style="left:122px;top:371px;width:198px"></div>
  <div class="abs label" style="left:5px;top:405px">Address 1</div>
  <div class="abs field" style="left:122px;top:405px;width:198px"></div>
  <div class="abs label" style="left:5px;top:439px">Address 2</div>
  <div class="abs field" style="left:122px;top:439px;width:198px"></div>
  <div class="abs label" style="left:5px;top:473px">Address 3</div>
  <div class="abs field" style="left:122px;top:473px;width:198px"></div>
  <div class="abs label" style="left:5px;top:507px">City</div>
  <div class="abs field" style="left:122px;top:507px;width:198px"></div>
  <div class="abs label" style="left:5px;top:543px">Select Country</div>
  <div class="abs field" style="left:122px;top:541px;width:198px"><div class="abs select-arrow">▼</div></div>
  <div class="abs label" style="left:5px;top:575px">State</div>
  <div class="abs field" style="left:122px;top:576px;width:198px"></div>
  <div class="abs label" style="left:5px;top:615px">Postal Code + 4</div>
  <div class="abs field" style="left:122px;top:614px;width:80px">11111</div>
  <div class="abs plus" style="left:207px;top:614px">+</div>
  <div class="abs field" style="left:224px;top:614px;width:96px">1111</div>

  <!-- Shipping Address -->
  <h2 class="abs section-head" style="left:366px;top:222px">Shipping Address</h2>
  <div class="abs section-rule" style="left:366px;top:249px;width:290px"></div>
  <div class="abs notch" style="left:375px;top:251px"></div>
  <div class="abs box" style="left:366px;top:270px"></div>
  <div class="abs same-text">Billing address is same as<br>shipping address</div>

  <div class="abs label wide" style="left:361px;top:329px">Street Address 1</div>
  <div class="abs field" style="left:466px;top:329px;width:190px"></div>
  <div class="abs label wide" style="left:361px;top:363px">Street Address 2</div>
  <div class="abs field" style="left:466px;top:363px;width:190px"></div>
  <div class="abs label wide" style="left:361px;top:397px">Street Address 3</div>
  <div class="abs field" style="left:466px;top:397px;width:190px"></div>
  <div class="abs label wide" style="left:361px;top:431px">City</div>
  <div class="abs field" style="left:466px;top:431px;width:190px"></div>
  <div class="abs label wide" style="left:361px;top:468px">Select Country</div>
  <div class="abs field" style="left:466px;top:466px;width:190px"><div class="abs select-arrow">▼</div></div>
  <div class="abs label wide" style="left:361px;top:500px">State</div>
  <div class="abs field" style="left:466px;top:500px;width:190px"></div>
  <div class="abs label wide" style="left:361px;top:534px">Postal Code + 4</div>
  <div class="abs field" style="left:466px;top:534px;width:80px">44444</div>
  <div class="abs plus" style="left:554px;top:534px">+</div>
  <div class="abs field" style="left:568px;top:534px;width:88px">2222</div>

  <div class="abs divider-mark"></div>

  <!-- Email preferences -->
  <div class="abs box" style="left:29px;top:787px"></div>
  <div class="abs subscribe">Subscribe me to your general email list</div>
  <div class="abs subscribe-note">This monthly email includes free video loops and VIP sale notices</div>
  <div class="abs filter-note">Help us filter our emails so we only sending relevant information to you</div>

  <div class="abs list-head" style="left:29px;top:874px;width:292px">Send me emails about these<br>product types:</div>
  <div class="abs list-notch" style="left:38px;top:928px"></div>
  <div class="abs list-head" style="left:363px;top:874px;width:292px">Send me emails about these<br>product types:</div>
  <div class="abs list-notch" style="left:372px;top:928px"></div>

  <div class="abs box" style="left:29px;top:950px"></div><div class="abs opt" style="left:55px;top:950px">Low energy motion loops</div>
  <div class="abs box" style="left:29px;top:977px"></div><div class="abs opt" style="left:55px;top:977px">High energy motion loops</div>
  <div class="abs box" style="left:29px;top:1005px"></div><div class="abs opt" style="left:55px;top:1005px">Timelapse footage</div>
  <div class="abs box" style="left:29px;top:1035px"></div><div class="abs opt" style="left:55px;top:1035px">Low energy motion loops</div>
  <div class="abs box" style="left:29px;top:1066px"></div><div class="abs opt" style="left:55px;top:1066px">High energy motion loops</div>
  <div class="abs box" style="left:29px;top:1097px"></div><div class="abs opt" style="left:55px;top:1097px">Timelapse footage</div>
  <div class="abs box" style="left:29px;top:1128px"></div><div class="abs opt" style="left:55px;top:1128px">Worship or wedding motion loops</div>
  <div class="abs box" style="left:29px;top:1159px"></div><div class="abs opt" style="left:55px;top:1159px">Pre-mixed DVDs and BluRay</div>
  <div class="abs box" style="left:29px;top:1190px"></div><div class="abs opt" style="left:55px;top:1190px">Entertainment lasers for concerts and clubs</div>
  <div class="abs box" style="left:29px;top:1222px"></div><div class="abs opt" style="left:55px;top:1222px">Entertainment lasers for text &amp; logo display</div>
  <div class="abs box" style="left:29px;top:1253px"></div><div class="abs opt" style="left:55px;top:1253px">Custom logo animation services</div>
  <div class="abs box" style="left:29px;top:1284px"></div><div class="abs opt" style="left:55px;top:1284px">Video software for creating video animations</div>
  <div class="abs box" style="left:29px;top:1315px"></div><div class="abs opt" style="left:55px;top:1315px">Video software for live performance (Vjing)</div>

  <div class="abs box" style="left:363px;top:950px"></div><div class="abs opt" style="left:388px;top:950px">VJing (live performance video)</div>
  <div class="abs box" style="left:363px;top:977px"></div><div class="abs opt" style="left:388px;top:977px">DJing (live performance audio+video)</div>
  <div class="abs box" style="left:363px;top:1005px"></div><div class="abs opt" style="left:388px;top:1005px">Performing in a band</div>
  <div class="abs box" style="left:363px;top:1035px"></div><div class="abs opt" style="left:388px;top:1035px">Video editing</div>
  <div class="abs box" style="left:363px;top:1066px"></div><div class="abs opt" style="left:388px;top:1066px">Corporate presentations</div>
  <div class="abs box" style="left:363px;top:1097px"></div><div class="abs opt" style="left:388px;top:1097px">Worship video services</div>
  <div class="abs box" style="left:363px;top:1128px"></div><div class="abs opt" style="left:388px;top:1128px">Lasers for entertainment &amp; branding</div>
  <div class="abs box" style="left:363px;top:1159px"></div><div class="abs opt" style="left:388px;top:1159px">Special offers from BrightVanta partners</div>

  <div class="abs unsubscribe"><span class="abs box"></span>Unsubscribe from all email lists</div>
  <div class="abs submit">Submit Now</div>

  <div class="abs footer"></div>
</div>
</body>
</html>
```